Business Card Design

I already have a company logo for my company. I have a logo for the manufacturer we represent. I want a professional business card design.

```html
<!DOCTYPE html>
<html lang="en">
<head>
<meta charset="utf-8">
<title>Business Card – Beacon Alert Co</title>
<link href="https://fonts.googleapis.com/css2?family=Open+Sans:wght@400;600;700&display=swap" rel="stylesheet">
<style>
  :root {
    --backdrop: #2a2a2a;
    --card-white: #ffffff;
    --card-black: #1c1c1c;
    --accent-red: #e3262b;
    --accent-gold: #c9a227;
    --ink: #3a3a3a;
    --ink-soft: #666666;
    --silver: #d6d6d6;
  }
  * { margin: 0; padding: 0; box-sizing: border-box; }
  html, body {
    width: 1200px; height: 900px; overflow: hidden;
    background: var(--backdrop);
    font-family: "Open Sans", Arial, sans-serif;
  }
  .sheet {
    width: 1200px; height: 900px;
    display: flex; flex-direction: column;
    align-items: center; justify-content: center; gap: 50px;
  }
  .card {
    width: 630px; height: 360px;
    border-radius: 26px;
    position: relative;
    overflow: hidden;
  }

  /* Front */
  .card--front { background: var(--card-white); }
  .front__emblem {
    position: absolute; left: 0; right: 0; top: 34px;
    display: flex; align-items: center; justify-content: center; gap: 16px;
  }
  .emblem__square {
    width: 78px; height: 78px; background: var(--accent-gold);
  }
  .emblem__name {
    font-weight: 700; font-size: 26px; color: var(--ink);
    text-transform: uppercase; letter-spacing: 1px;
  }
  .front__person {
    position: absolute; left: 78px; top: 160px;
  }
  .person__name {
    color: var(--accent-red); font-weight: 700; font-size: 25px; line-height: 1.1;
  }
  .person__role {
    color: var(--ink-soft); font-size: 13px; margin-top: 4px;
  }
  .front__divider {
    position: absolute; left: 300px; top: 196px;
    width: 2px; height: 74px; background: var(--accent-gold);
  }
  .front__contacts {
    position: absolute; left: 314px; top: 196px;
    list-style: none;
  }
  .contact {
    display: flex; align-items: center; gap: 9px;
    font-size: 14px; color: var(--ink); margin-bottom: 7px;
  }
  .contact__icon { width: 16px; height: 16px; flex: none; }
  .front__wordmark {
    position: absolute; left: 78px; bottom: 34px;
    font-weight: 700; font-size: 24px; color: var(--accent-red);
    text-transform: uppercase; letter-spacing: 1px;
  }

  /* Back */
  .card--back {
    background: var(--card-black);
    display: flex; align-items: center; justify-content: center; gap: 16px;
  }
  .back__square {
    width: 56px; height: 56px; background: var(--accent-gold);
  }
  .back__name {
    font-weight: 700; font-size: 30px; color: var(--silver);
    text-transform: uppercase; letter-spacing: 1px;
  }
</style>
</head>
<body>
<main class="sheet">
  <section class="card card--front" aria-label="Business card front">
    <div class="front__emblem">
      <span class="emblem__square"></span>
      <span class="emblem__name">Beacon Alert Co</span>
    </div>

    <div class="front__person">
      <h1 class="person__name">Daniel Harper</h1>
      <p class="person__role">Managing Director</p>
    </div>

    <div class="front__divider"></div>

    <ul class="front__contacts">
      <li class="contact">
        <svg class="contact__icon" viewBox="0 0 18 18" aria-hidden="true">
          <rect width="18" height="18" rx="3" fill="#e3262b"/>
          <path d="M6 4.5h2l1 2.5-1.3 1a6 6 0 0 0 2.3 2.3l1-1.3 2.5 1v2c0 .6-.5 1-1 1A8 8 0 0 1 5 5.5c0-.5.4-1 1-1z" fill="#fff"/>
        </svg>
        555.210.4879
      </li>
      <li class="contact">
        <svg class="contact__icon" viewBox="0 0 18 18" aria-hidden="true">
          <rect width="18" height="18" rx="3" fill="#e3262b"/>
          <rect x="4" y="5.5" width="10" height="7" fill="none" stroke="#fff" stroke-width="1.3"/>
          <path d="M4 5.5l5 4 5-4" fill="none" stroke="#fff" stroke-width="1.3"/>
        </svg>
        hello@beaconalertco.com
      </li>
      <li class="contact">
        <svg class="contact__icon" viewBox="0 0 18 18" aria-hidden="true">
          <rect width="18" height="18" rx="3" fill="#e3262b"/>
          <circle cx="9" cy="9" r="5" fill="none" stroke="#fff" stroke-width="1.2"/>
          <ellipse cx="9" cy="9" rx="2.2" ry="5" fill="none" stroke="#fff" stroke-width="1"/>
          <path d="M4 9h10" stroke="#fff" stroke-width="1"/>
        </svg>
        www.beaconalertco.com
      </li>
    </ul>

    <p class="front__wordmark">Beacon Alert Co</p>
  </section>

  <section class="card card--back" aria-label="Business card back">
    <span class="back__square"></span>
    <span class="back__name">Beacon Alert Co</span>
  </section>
</main>
</body>
</html>
```